New Bicycle shop business card

Hi!
I'm looking for a business card for my new proffesional bike mechanics shop. This shop is only for fixing broken bikes and not selling bikes.
Peferbly a modern and sleek and modern design.
Colors: black, grey, red, white
Information:
Name: Rijwielwerkplaats Vanhoutte
Shop owner: Bart Vanhoutte & Marieke Segers
Website: www.rijwielwerkplaats-vanhoutte.be
Email: info@rijwielwerkplaats-vanhoutte.be
Phone number: +32471902368
Street adres: Kerkweg 46
9940 Bellebeke
Slogan/shop information: Herstellingen van alle merken.
Logo: see files.
Target Market(s)
People who seek a mechanic to fix or upgrade their bikes.
Contact Information for Business Card
Information:
Website: info@rijwielwerkplaats-vanhoutte.be
9940 Bellebeke
Logo: see files.

```html
<!DOCTYPE html>
<html lang="nl">
<head>
<meta charset="utf-8">
<title>Rijwielwerkplaats Vanhoutte – visitekaartje</title>
<link rel="stylesheet" href="https://fonts.googleapis.com/css2?family=Roboto:wght@400;500;700;900&display=swap">
<style>
  :root {
    --bg: #2e2e2f;
    --card: #1d1d1f;
    --card-edge: #262628;
    --red: #e0283a;
    --white: #ffffff;
    --grey: #a9acaf;
    --muted: #c9c9cb;
    --faint: rgba(255,255,255,0.035);
  }
  * { box-sizing: border-box; margin: 0; padding: 0; }
  html, body { width: 799px; height: 1200px; overflow: hidden; }
  body {
    background: var(--bg);
    font-family: "Roboto", Arial, sans-serif;
    color: var(--white);
    position: relative;
  }
  .card {
    position: absolute;
    left: 80px;
    width: 640px;
    height: 366px;
    background: var(--card);
    border-radius: 22px;
    overflow: hidden;
    box-shadow: 0 14px 34px rgba(0,0,0,0.45);
  }
  .card--front { top: 130px; }
  .card--back { top: 640px; }

  .brand { display: flex; align-items: center; gap: 14px; }
  .brand__mark { width: 40px; height: 40px; background: var(--red); flex: none; }
  .brand__name {
    font-weight: 900;
    text-transform: uppercase;
    letter-spacing: 1px;
    color: var(--white);
    line-height: 1.1;
  }

  /* front */
  .front__brand {
    position: absolute;
    top: 118px; left: 0; right: 0;
    flex-direction: column;
    gap: 18px;
  }
  .front__brand .brand__mark { width: 48px; height: 48px; }
  .front__brand .brand__name { font-size: 27px; text-align: center; }
  .front__web {
    position: absolute;
    top: 262px; left: 0; right: 0;
    text-align: center;
    font-size: 17px;
    color: var(--muted);
  }
  .accent { color: var(--red); }

  /* back */
  .back__decor {
    position: absolute;
    right: -70px; top: 90px;
    width: 330px; height: 330px;
    border-radius: 50%;
    background: var(--faint);
  }
  .back__brand { position: absolute; top: 34px; left: 36px; }
  .back__brand .brand__name { font-size: 22px; }
  .person { position: absolute; top: 120px; left: 36px; }
  .person__name {
    font-size: 22px; font-weight: 900; text-transform: uppercase;
    color: var(--red); letter-spacing: 0.5px;
  }
  .person__role { font-size: 13px; color: var(--muted); margin-top: 2px; }
  .address {
    position: absolute; top: 192px; left: 36px;
    font-size: 15px; line-height: 1.45; color: var(--white);
    font-style: normal;
  }
  .contacts {
    position: absolute; top: 204px; left: 300px;
    list-style: none; font-size: 14.5px; line-height: 1;
  }
  .contacts li { display: flex; align-items: center; gap: 12px; margin-bottom: 10px; }
  .contacts svg { width: 14px; height: 14px; fill: var(--red); flex: none; }
  .base-strip {
    position: absolute; left: 0; bottom: 0;
    width: 100%; height: 12px; background: var(--grey);
  }
  .slogan-band {
    position: absolute; right: 0; bottom: 0;
    width: 390px; height: 58px;
    background: var(--red);
    border-top-left-radius: 20px;
    display: flex; align-items: center; justify-content: center;
    font-size: 17px; font-weight: 500; color: var(--white);
  }
</style>
</head>
<body>

<section class="card card--front" aria-label="Voorzijde visitekaartje">
  <div class="brand front__brand">
    <span class="brand__mark"></span>
    <span class="brand__name">Rijwielwerkplaats Vanhoutte</span>
  </div>
  <p class="front__web">www.rijwielwerkplaats-<span class="accent">vanhoutte</span>.be</p>
</section>

<section class="card card--back" aria-label="Achterzijde visitekaartje">
  <div class="back__decor"></div>
  <div class="brand back__brand">
    <span class="brand__mark"></span>
    <span class="brand__name">Rijwielwerkplaats Vanhoutte</span>
  </div>

  <div class="person">
    <p class="person__name">Marieke Segers</p>
    <p class="person__role">Owner</p>
  </div>

  <address class="address">Kerkweg 46<br>9940 Bellebeke</address>

  <ul class="contacts">
    <li>
      <svg viewBox="0 0 24 24" aria-hidden="true"><path d="M6.6 10.8a15.1 15.1 0 0 0 6.6 6.6l2.2-2.2c.3-.3.7-.4 1-.2 1.1.4 2.3.6 3.6.6.6 0 1 .4 1 1V20c0 .6-.4 1-1 1A17 17 0 0 1 3 4c0-.6.4-1 1-1h3.5c.6 0 1 .4 1 1 0 1.3.2 2.5.6 3.6.1.3 0 .7-.2 1z"/></svg>
      +32471902368
    </li>
    <li>
      <svg viewBox="0 0 24 24" aria-hidden="true"><path d="M2 5h20v14H2z M4 7v.5l8 5 8-5V7l-8 5z" fill-rule="evenodd"/></svg>
      www.rijwielwerkplaats-vanhoutte.be
    </li>
    <li>
      <svg viewBox="0 0 24 24" aria-hidden="true"><path d="M12 2a10 10 0 1 0 0 20 10 10 0 0 0 0-20zm6.9 9h-3a15 15 0 0 0-1.3-5.6A8 8 0 0 1 18.9 11zM12 4.1c.9 1.2 1.8 3.5 2 6.9h-4c.2-3.4 1.1-5.7 2-6.9zM9.4 5.4A15 15 0 0 0 8.1 11h-3a8 8 0 0 1 4.3-5.6zM5.1 13h3a15 15 0 0 0 1.3 5.6A8 8 0 0 1 5.1 13zm6.9 6.9c-.9-1.2-1.8-3.5-2-6.9h4c-.2 3.4-1.1 5.7-2 6.9zm2.6-1.3a15 15 0 0 0 1.3-5.6h3a8 8 0 0 1-4.3 5.6z"/></svg>
      info@rijwielwerkplaats-vanhoutte.be
    </li>
  </ul>

  <div class="base-strip"></div>
  <p class="slogan-band">Herstellingen van alle merken</p>
</section>

</body>
</html>
```